VANTA Brouchure's

Project Overview:

We are seeking your expertise in designing a series of brochures for VANTA Systemworks. These brochures will be distributed to both current and prospective customers and need to effectively showcase our offerings in automation technology.

Requirements:

Image Utilization:

We have uploaded up to 40 images, which we have paid for and would like to see creatively arranged across different brochure designs.
The images should be utilized to emphasize key aspects of our business, including programming, design, robotics, PLC, and support.
Branding:

The VANTA Systemworks logo must be prominently displayed on both the front and back covers of each brochure for consistent branding.
Focus Areas:

Some brochures should specifically highlight our expertise in robotic solutions, particularly focusing on AGV and AMR technologies.
Additionally, our partnership with Morilendo and our capabilities in robotic arm technologies should be emphasized.
Contact Information:

Please include the following contact emails on each brochure: sales@vantasystemworks.example and admin@vantasystemworks.example.
We look forward to seeing your design concepts that align with our brand and effectively communicate our technological capabilities.

Also, please see attached a mock brochure, please use the wording for context.

```html
<!DOCTYPE html>
<html lang="en">
<head>
<meta charset="utf-8">
<title>VANTA Systemworks – Services Flyer</title>
<link rel="stylesheet" href="https://fonts.googleapis.com/css2?family=Roboto:wght@300;400;500;700;900&family=Raleway:wght@500;600&display=swap">
<style>
  :root {
    --stage: #dde5ee;
    --blue-left: #2a90d8;
    --blue-mid: #1c7dca;
    --blue-right: #1870c4;
    --blue-deep: #1a4fb8;
    --heading-blue: #1b3fae;
    --ink: #111318;
    --muted: #55606e;
    --white: #ffffff;
    --photo-a: #8a9aa8;
    --photo-b: #b9c2c9;
  }
  * { margin: 0; padding: 0; box-sizing: border-box; }
  html, body { width: 1200px; height: 861px; overflow: hidden; }
  body { background: var(--stage); font-family: "Roboto", Arial, sans-serif; }

  .flyer {
    position: absolute; left: 326px; top: 20px;
    width: 548px; height: 822px; overflow: hidden;
    background: var(--white);
    box-shadow: 0 6px 18px rgba(20, 40, 70, .25);
  }
  .flyer__imagery {
    position: absolute; left: 0; top: 420px; width: 548px; height: 402px;
    background: linear-gradient(160deg, #eef0f8 0%, #d9dff0 45%, #e7e9f4 70%, #f4f5fa 100%);
  }
  .flyer__shapes { position: absolute; inset: 0; }

  .t { position: absolute; color: var(--white); white-space: nowrap; line-height: 1; }
  .center { transform: translateX(-50%); text-align: center; }

  .section-title { font-weight: 500; font-size: 15.5px; letter-spacing: .1px; }
  .section-title::after {
    content: ""; display: block; height: 2px; background: var(--white);
    width: 74%; margin: 4px auto 0;
  }
  .section-title--two { line-height: 1.25; }
  .brand-label { font-weight: 500; font-size: 8px; }
  .group-label { font-weight: 400; font-size: 8px; }
  .item { font-weight: 300; font-size: 8.2px; line-height: 1.3; }
  .item::before { content: "•"; position: absolute; left: -15px; font-size: 6px; top: 1px; }

  .contact {
    position: absolute; right: 33px; top: 456px; text-align: right;
    font-family: "Raleway", Arial, sans-serif; font-weight: 500;
    color: var(--ink); font-size: 15.5px; line-height: 17.6px;
  }

  .industries-title {
    position: absolute; left: 274px; top: 548px; transform: translateX(-50%);
    font-weight: 900; font-size: 23.5px; color: var(--heading-blue); white-space: nowrap;
  }
  .industries {
    position: absolute; left: 61px; top: 582px; width: 425px; height: 132px;
    border: 2px solid var(--ink); border-radius: 11px;
  }
  .industry {
    position: absolute; transform: translate(-50%, -50%);
    font-weight: 500; font-size: 12.3px; color: var(--ink); white-space: nowrap;
  }

  .tagline {
    position: absolute; left: 274px; transform: translateX(-50%);
    white-space: nowrap; text-align: center;
  }
  .tagline--caps { top: 725px; font-size: 7.6px; font-weight: 300; color: var(--muted); }
  .tagline--sub { top: 738px; font-size: 8.2px; font-weight: 400; color: var(--ink); }

  .brand {
    position: absolute; left: 29px; top: 764px; display: flex; align-items: center; gap: 6px;
    font-weight: 900; color: var(--heading-blue); font-size: 17px; line-height: 1;
  }
  .brand__dot { width: 12px; height: 12px; border-radius: 50%; background: var(--heading-blue); }
  .brand__name span { display: block; font-size: 17px; }
  .brand__name span + span { font-size: 10.5px; letter-spacing: 1.3px; margin-top: 2px; }

  .website {
    position: absolute; left: 166px; top: 791px;
    font-family: "Raleway", Arial, sans-serif; font-weight: 500;
    font-size: 14.5px; color: var(--ink);
  }
</style>
</head>
<body>
<main class="flyer">
  <div class="flyer__imagery" role="img" aria-label="Soft background image of a robotic arm over circuitry"></div>

  <svg class="flyer__shapes" viewBox="0 0 548 822" width="548" height="822" aria-hidden="false">
    <polygon points="0,0 198,0 198,510 0,564" fill="var(--blue-left)"/>
    <polygon points="198,156 368,111 368,433 198,497" fill="var(--blue-mid)"/>
    <polygon points="358,96 548,48 548,389 368,433" fill="var(--blue-right)"/>
    <polygon points="0,61 187,20 187,172 0,225" fill="var(--photo-a)" role="img" aria-label="Technician checking a control panel with a tablet"/>
    <polygon points="187,0 360,0 360,112 187,172" fill="var(--photo-b)" role="img" aria-label="Wired control cabinet with terminal rows"/>
    <polygon points="360,0 548,0 548,48 360,96" fill="#9fb0c2" role="img" aria-label="Engineer at monitors showing process screens"/>
    <polygon points="350,822 548,753 548,822" fill="var(--blue-deep)"/>
  </svg>

  <!-- Programming -->
  <div class="t center section-title" style="left:98px; top:243px;">PROGRAMMING</div>
  <div class="t center brand-label" style="left:98px; top:281px;">BRIGHTWELL</div>
  <div class="t group-label" style="left:49px; top:305px;">Hardware:</div>
  <div class="t item" style="left:79px; top:316px;">Torquemax Drives</div>
  <div class="t item" style="left:79px; top:327px;">Strata Logic</div>
  <div class="t item" style="left:79px; top:338px;">Mini Logic</div>
  <div class="t group-label" style="left:49px; top:349px;">Software:</div>
  <div class="t item" style="left:79px; top:360px;">Forge Studio 7</div>
  <div class="t item" style="left:79px; top:371px;">PlantSpeak View</div>
  <div class="t center brand-label" style="left:98px; top:394px;">LUMENFIELD AUTOMATION</div>
  <div class="t group-label" style="left:49px; top:416px;">Software</div>
  <div class="t item" style="left:79px; top:428px;">Kindle SCADA</div>
  <div class="t center brand-label" style="left:98px; top:450px;">TELSEN, ORVIK</div>
  <div class="t center brand-label" style="left:98px; top:472px;">IO/MOTOR Checksheets</div>
  <div class="t center brand-label" style="left:98px; top:494px;">Alarm Reports</div>

  <!-- Design -->
  <div class="t center section-title" style="left:278px; top:173px;">DESIGN</div>
  <div class="t center brand-label" style="left:278px; top:217px;">SCHEMIO</div>
  <div class="t item" style="left:241px; top:240px;">Cloud-based Program</div>
  <div class="t item" style="left:241px; top:262px;">Smart PDFs</div>

  <!-- Project management -->
  <div class="t center section-title section-title--two" style="left:282px; top:317px;">PROJECT<br>MANAGEMENT</div>
  <div class="t item" style="left:241px; top:389px;">Custom Dashboards</div>
  <div class="t item" style="left:241px; top:411px;">Digital Service Reports</div>

  <!-- Fabrication -->
  <div class="t center section-title" style="left:458px; top:111px;">FABRICATION</div>
  <div class="t item" style="left:419px; top:140px;">Automated Tooling</div>
  <div class="t item" style="left:419px; top:162px;">Custom Panel Fabrication</div>
  <div class="t item" style="left:419px; top:184px;">High-Quality Materials</div>
  <div class="t item" style="left:419px; top:206px;">Maintenance Support</div>
  <div class="t item" style="left:419px; top:228px;">Expert Craftsmanship</div>

  <!-- Safety -->
  <div class="t center section-title section-title--two" style="left:458px; top:254px;">SAFEY &amp;<br>COMPLIANCE</div>
  <div class="t item" style="left:423px; top:326px;">Precommisioning<br>Checks</div>
  <div class="t item" style="left:423px; top:359px;">Functional Safety<br>Checks</div>

  <address class="contact" style="font-style:normal;">
    318 Alder Rd<br>
    555-014-2870<br>
    sales@vantasystemworks.example<br>
    admin@vantasystemworks.example
  </address>

  <h2 class="industries-title">INDUSTRIES SERVED</h2>
  <div class="industries">
    <span class="industry" style="left:72px; top:17px;">Wood Processing</span>
    <span class="industry" style="left:225px; top:17px;">Asphalt Production</span>
    <span class="industry" style="left:370px; top:17px;">Automotive</span>
    <span class="industry" style="left:72px; top:48px;">Steel</span>
    <span class="industry" style="left:225px; top:48px;">Pulp &amp; Paper</span>
    <span class="industry" style="left:370px; top:48px;">Biomass</span>
    <span class="industry" style="left:72px; top:79px;">Food &amp; Beverage</span>
    <span class="industry" style="left:225px; top:79px;">Packaging</span>
    <span class="industry" style="left:370px; top:79px;">Agriculture</span>
    <span class="industry" style="left:72px; top:110px;">Recycling</span>
    <span class="industry" style="left:225px; top:110px;">Textiles</span>
    <span class="industry" style="left:370px; top:110px;">&amp; More</span>
  </div>

  <p class="tagline tagline--caps">LEADING-EDGE AUTOMATION SERVICES IN SOUTHEASTERN ALABAMA FOR ALL MANUFACTUERERS</p>
  <p class="tagline tagline--sub">Setting the standard for process engineering and automation services since 1997</p>

  <div class="brand">
    <span class="brand__dot"></span>
    <span class="brand__name"><span>VANTA</span><span>SYSTEMWORKS</span></span>
  </div>
  <div class="website">vantasystemworks.example</div>
</main>
</body>
</html>
```